Mobile Fitness snd Therapy Business Card Design

I need a business card designed for my mobile fitness and therapy business.

Please view the images that I have uploaded. I like the simplicity of the design that I have attached. I adapted it with my information

Target Market(s)

Those seeking personal training, injury rehabilitation or massage therapy.

Industry/Entity Type

Business

Contact Information for Business Card

Derek Fulham - MSc, CAT(C), RMT, CSCS, Pn2
e-mail: derek@vantrelo.com
website: www.vantrelo.com
instagram: @derek_fulham

Font styles to use
Sans Serif

Colors
3176b5
0355a3

Requirements
Must have
• "Contact us to receive a FREE assessment"
• Services offered:
• Personal Training
• Golf Fitness
• Injury Rehab
• Massage Therapy
• Yoga
Nice to have
• Consistent colours with brand
• - Dark Blue: #232837
• - Blue: #5096f0
• Consistent look/feel with the website: www.vantrelo.com

```html
<!DOCTYPE html>
<html lang="en">
<head>
<meta charset="utf-8">
<title>Vantrelo Business Card</title>
<link rel="stylesheet" href="https://fonts.googleapis.com/css2?family=Arimo:wght@400;700&display=swap">
<style>
  :root {
    --backdrop: #555555;
    --card-white: #ffffff;
    --ink-dark: #232837;
    --ink-body: #2b2b2b;
    --accent-blue: #1f4fd1;
    --rule-grey: #bdbdbd;
    --back-deep: #4b79c4;
    --back-light: #92bbe8;
    --back-mid: #6f9ad8;
  }
  * { margin: 0; padding: 0; box-sizing: border-box; }
  html, body {
    width: 1200px; height: 900px; overflow: hidden;
    background: var(--backdrop);
    font-family: "Arimo", Arial, sans-serif;
  }
  .canvas { position: relative; width: 1200px; height: 900px; }
  .card {
    position: absolute; top: 170px; width: 347px; height: 561px;
    text-align: center;
  }
  .card-front { left: 259px; background: var(--card-white); }
  .card-back {
    left: 631px; color: #fff;
    background:
      radial-gradient(ellipse 70% 55% at 30% 62%, var(--back-light) 0%, rgba(146,187,232,0) 70%),
      linear-gradient(160deg, var(--back-deep) 0%, var(--back-mid) 45%, var(--back-light) 70%, var(--back-deep) 100%);
  }
  .brand {
    position: absolute; top: 154px; left: 0; right: 0;
    display: flex; align-items: center; justify-content: center; gap: 10px;
  }
  .brand-mark { width: 16px; height: 16px; background: var(--accent-blue); }
  .brand-name {
    font-weight: 700; font-size: 34px; letter-spacing: 3px; color: var(--ink-dark);
  }
  .tagline {
    position: absolute; top: 197px; left: 0; right: 0;
    font-weight: 700; font-size: 12px; letter-spacing: 2.2px; color: var(--ink-dark);
  }
  .contact { position: absolute; top: 370px; left: 0; right: 0; }
  .person-name { font-weight: 700; font-size: 21px; color: var(--accent-blue); line-height: 24px; }
  .credentials { font-size: 15px; color: var(--ink-body); margin-top: 3px; line-height: 18px; }
  .rule { width: 194px; height: 1px; background: var(--rule-grey); margin: 12px auto; }
  .contact-line { font-size: 15px; color: var(--ink-body); line-height: 23px; }
  .label { font-weight: 700; color: var(--accent-blue); }
  .back-heading {
    position: absolute; top: 356px; left: 0; right: 0;
    font-weight: 700; font-size: 18px; line-height: 23px; letter-spacing: 0.2px;
  }
  .services-title {
    position: absolute; top: 430px; left: 0; right: 0;
    font-weight: 700; font-size: 15px;
  }
  .services-list {
    position: absolute; top: 468px; left: 0; right: 0;
    font-size: 14px; line-height: 18px; list-style: none;
  }
</style>
</head>
<body>
<main class="canvas">
  <section class="card card-front" aria-label="Business card front">
    <div class="brand">
      <span class="brand-mark" aria-hidden="true"></span>
      <span class="brand-name">VANTRELO</span>
    </div>
    <p class="tagline">NUTRITION - FITNESS - HEALTH</p>
    <div class="contact">
      <p class="person-name">DEREK FULHAM</p>
      <p class="credentials">MSc, CAT(C), RMT, CSCS, Pn2</p>
      <div class="rule"></div>
      <p class="contact-line"><span class="label">E :</span>derek@vantrelo.com</p>
      <p class="contact-line"><span class="label">W :</span>www.vantrelo.com</p>
      <div class="rule"></div>
      <p class="contact-line"><span class="label">INSTAGRAM :</span> @derek_fulham</p>
    </div>
  </section>

  <section class="card card-back" aria-label="Business card back">
    <p class="back-heading">CONTACT US TO RECEIVE A<br>FREE ASSESSMENT</p>
    <p class="services-title">SERVICES OFFERED:</p>
    <ul class="services-list">
      <li>PERSONAL TRAINING &nbsp;|&nbsp; GOLF FITNESS</li>
      <li>INJURY REHAB | MASSAGE THERAPY</li>
      <li>YOGA</li>
    </ul>
  </section>
</main>
</body>
</html>
```